Harborview Estates Business Card for Apartment Buildings

Create business cards for resident managers who run apartment buildings. The audience is the public who are searching for apartment rentals, and current residents who live at the apartment building. Key design element will be incorporating the company logo, however, the logo cannot dominate. The building name and manager name are more important than the logo. Current business card design leaves little room for copy, so we may need to reduce the size on the current card to allow for more space for copy.

Target Market(s)

Adults 18-65 years of age, who are looking for an apartment rental, plus current residents who live at our apartment buildings.

Industry/Entity Type

Property Management

Contact Information for Business Card

A major design element will be use of the company logo. Important property and manager contact information must be part of the design. The size of the logo will need to be reduced to make room for building and manager contact copy.

Font styles to use
Sans Serif

Colors
3176b5
000000
959595
ffffff

Requirements
Must have
• 1) Incorporate the company logo.
• 2) Use the company colors (dark blue, black/grey, over white).
• 3) FEATURE THE BUILDING NAME
• 4) FEATURE THE MANAGER NAME
• 5) The company name is less important than BUILDING and MANAGER
• 6) Manager contact information
• **SEE ATTACHED CREATIVE BRIEF**
Nice to have
• 1) Back of card logo watermark
• 2) Ability to write notes on back of carfd
Should not have
• Avoid letting the company logo dominate the card, the building name and manager are more important than the company logo.

```html
<!DOCTYPE html>
<html lang="en">
<head>
<meta charset="utf-8">
<title>Harborview Estates – Business Card</title>
<link href="https://fonts.googleapis.com/css2?family=Lato:wght@400;700;900&display=swap" rel="stylesheet">
<style>
  :root {
    --brand-blue: #1f6fb2;
    --ink: #222222;
    --grey: #444447;
    --white: #ffffff;
    --backdrop: #e9e9e9;
  }
  * { margin: 0; padding: 0; box-sizing: border-box; }
  html, body { width: 1200px; height: 930px; overflow: hidden; }
  body {
    background: var(--backdrop);
    font-family: "Lato", sans-serif;
    position: relative;
  }
  .card {
    position: absolute;
    width: 540px;
    height: 309px;
    overflow: hidden;
    box-shadow: 0 6px 18px rgba(0,0,0,0.18);
  }

  /* Back of card */
  .card-back {
    left: 50px;
    top: 170px;
    background: var(--brand-blue);
  }
  .card-back .brand {
    position: absolute;
    left: 0; right: 0;
    top: 104px;
    display: flex;
    justify-content: center;
    align-items: center;
    gap: 16px;
  }
  .brand-mark { flex: none; }
  .card-back .brand-mark { background: var(--white); width: 52px; height: 52px; }
  .brand-name {
    font-weight: 900;
    letter-spacing: 1px;
    line-height: 1.05;
  }
  .card-back .brand-name { color: var(--white); font-size: 30px; }
  .card-back .web {
    position: absolute;
    left: 0; right: 0;
    top: 232px;
    text-align: center;
    color: var(--white);
    font-size: 13px;
    letter-spacing: 0.5px;
  }

  /* Front of card */
  .card-front {
    left: 610px;
    top: 450px;
    background: var(--white);
  }
  .card-front .brand {
    position: absolute;
    left: 40px;
    top: 128px;
    display: flex;
    align-items: center;
    gap: 12px;
  }
  .card-front .brand-mark { background: var(--brand-blue); width: 40px; height: 40px; }
  .card-front .brand-name { color: var(--brand-blue); font-size: 22px; }
  .divider {
    position: absolute;
    left: 262px;
    top: 48px;
    width: 1.5px;
    height: 188px;
    background: var(--brand-blue);
  }
  .contact {
    position: absolute;
    left: 282px;
    top: 44px;
    color: var(--ink);
  }
  .manager-name {
    color: var(--brand-blue);
    font-weight: 900;
    font-size: 19px;
    line-height: 1.1;
  }
  .manager-title { font-size: 11.5px; color: var(--grey); margin-bottom: 8px; }
  .building-name {
    color: var(--brand-blue);
    font-weight: 900;
    font-size: 15px;
    line-height: 1.15;
  }
  .address { font-size: 12px; line-height: 1.3; margin-bottom: 8px; }
  .contact-list { list-style: none; font-size: 12px; line-height: 1.55; }
  .contact-list li { display: flex; align-items: center; gap: 8px; }
  .contact-list svg { width: 11px; height: 11px; fill: var(--brand-blue); flex: none; }
  .bands {
    position: absolute;
    left: 0; bottom: 0;
    width: 540px;
    height: 50px;
  }
</style>
</head>
<body>

<section class="card card-back" aria-label="Back of business card">
  <div class="brand">
    <span class="brand-mark"></span>
    <span class="brand-name">HARBORVIEW<br>ESTATES</span>
  </div>
  <p class="web">www.harborviewest.com</p>
</section>

<section class="card card-front" aria-label="Front of business card">
  <div class="brand">
    <span class="brand-mark"></span>
    <span class="brand-name">HARBORVIEW<br>ESTATES</span>
  </div>

  <div class="divider"></div>

  <div class="contact">
    <p class="manager-name">Marisol Vega</p>
    <p class="manager-title">Resident Manager</p>
    <p class="building-name">Linden Court Apartments</p>
    <p class="address">2245 Maple Avenue<br>Bayside, CA 90417</p>
    <ul class="contact-list">
      <li>
        <svg viewBox="0 0 24 24" aria-label="Phone"><path d="M6.6 10.8a15.1 15.1 0 0 0 6.6 6.6l2.2-2.2a1 1 0 0 1 1-.25 11.4 11.4 0 0 0 3.6.57 1 1 0 0 1 1 1V20a1 1 0 0 1-1 1A17 17 0 0 1 3 4a1 1 0 0 1 1-1h3.5a1 1 0 0 1 1 1c0 1.25.2 2.45.57 3.57a1 1 0 0 1-.25 1z"/></svg>
        555-201-4410
      </li>
      <li>
        <svg viewBox="0 0 24 24" aria-label="Fax"><path d="M6 2h9l3 3v4H6z M3 10h18v9H3z M7 19h10v3H7z"/></svg>
        555-318-2074
      </li>
      <li>
        <svg viewBox="0 0 24 24" aria-label="Mobile"><path d="M7 1h10a2 2 0 0 1 2 2v18a2 2 0 0 1-2 2H7a2 2 0 0 1-2-2V3a2 2 0 0 1 2-2zm0 3v14h10V4z"/></svg>
        555-644-9120
      </li>
      <li>
        <svg viewBox="0 0 24 24" aria-label="Email"><path d="M2 5h20v14H2zm2 2v.5l8 5 8-5V7zm0 3v7h16v-7l-8 5z"/></svg>
        marisol@harborviewest.com
      </li>
      <li>
        <svg viewBox="0 0 24 24" aria-label="Website"><path d="M12 2a10 10 0 1 0 0 20 10 10 0 0 0 0-20zm0 2c1.2 1.4 2 3.6 2.2 7H9.8C10 7.6 10.8 5.4 12 4zm-2.2 9h4.4c-.2 3.4-1 5.6-2.2 7-1.2-1.4-2-3.6-2.2-7zM4.1 11a8 8 0 0 1 4-6.1A15 15 0 0 0 7.8 11zm0 2h3.7c.1 2.3.5 4.4 1.300 6.1A8 8 0 0 1 4.1 13zm12.1-2a15 15 0 0 0-1.3-6.1 8 8 0 0 1 4 6.1zm0 2h2.7a8 8 0 0 1-4 6.1c.8-1.7 1.2-3.8 1.3-6.1z"/></svg>
        www.harborviewest.com
      </li>
    </ul>
  </div>

  <svg class="bands" viewBox="0 0 540 50" preserveAspectRatio="none" aria-hidden="true">
    <polygon points="0,38 372,38 366,50 0,50" fill="var(--grey)"/>
    <polygon points="382,0 540,0 540,50 372,50" fill="var(--brand-blue)"/>
  </svg>
</section>

</body>
</html>
```